Awesome photographers card for an awesome new business

Double sided business card Black background and silver logo in middle on one side. Details on otherside. please keep it simple

Industry/Entity Type

Photographer

Contact Information for Business Card

Gerald Fenwick
0452817360
GeraldFenwickPhotography47@mailbox.test
www.GeraldFenwickPhotography.test.au
Instagram _Gerald_fenwick

Requirements
Must have
• My logo in Silver
• please use instagram logo instead of "Instagram"

```html
<!DOCTYPE html>
<html lang="en">
<head>
<meta charset="utf-8">
<title>Gerald Fenwick Photography – Business Card</title>
<link rel="stylesheet" href="https://fonts.googleapis.com/css2?family=Source+Sans+3:wght@400;600&display=swap">
<style>
  :root {
    --stage: #000000;
    --card-light: #f2f2f2;
    --card-dark: #1c1c1c;
    --ink: #1a1a1a;
    --silver: #d4d4d4;
  }
  * { margin: 0; padding: 0; box-sizing: border-box; }
  html, body {
    width: 1200px;
    height: 900px;
    overflow: hidden;
    background: var(--stage);
  }
  .stage {
    position: relative;
    width: 1200px;
    height: 900px;
    font-family: "Source Sans 3", "Myriad Pro", Arial, sans-serif;
  }
  .card {
    position: absolute;
    top: 200px;
    width: 310px;
    height: 502px;
  }
  .card--front {
    left: 265px;
    background: var(--card-light);
    border-radius: 66px 0 66px 0;
    color: var(--ink);
    text-align: center;
  }
  .card--back {
    left: 641px;
    width: 309px;
    background: var(--card-dark);
    border-radius: 0 66px 0 66px;
  }
  .holder-name {
    position: absolute;
    top: 379px;
    top: 179px;
    left: 0;
    right: 0;
    font-size: 19px;
    font-weight: 600;
  }
  .contact-list {
    position: absolute;
    top: 255px;
    left: 0;
    right: 0;
    list-style: none;
    font-size: 14.5px;
    line-height: 21px;
  }
  .brand-mark {
    position: absolute;
    left: 42px;
    top: 137px;
    width: 226px;
    height: 226px;
  }
  .brand-ring {
    fill: none;
    stroke: var(--silver);
    stroke-width: 4;
  }
  .brand-name {
    fill: var(--silver);
    font-family: "Source Sans 3", "Myriad Pro", Arial, sans-serif;
    font-size: 25px;
    font-weight: 400;
    letter-spacing: 1px;
  }
</style>
</head>
<body>
<main class="stage">
  <section class="card card--front" aria-label="Card front with contact details">
    <h1 class="holder-name">Gerald Fenwick</h1>
    <ul class="contact-list">
      <li class="contact-phone">0452817360</li>
      <li class="contact-email">GeraldFenwickPhotography47@mailbox.test</li>
      <li class="contact-web">www.GeraldFenwickPhotography.test.au</li>
      <li class="contact-social">Gerald_fenwick</li>
    </ul>
  </section>

  <section class="card card--back" aria-label="Card back with brand mark">
    <svg class="brand-mark" viewBox="0 0 226 226" aria-label="Gerald Fenwick">
      <circle class="brand-ring" cx="113" cy="113" r="109"/>
      <text class="brand-name" x="113" y="122" text-anchor="middle">Gerald Fenwick</text>
    </svg>
  </section>
</main>
</body>
</html>
```